Business Card for Industrial Distributor

We need a business card design for an industrial distributor. We sell machine parts for the manufacturing and oil industry. We would like the cards to look clean and modern but with a touch of industry.

Our colors are blue/white.

Please feel free to visit our website www.korvelpartsco.com

Target Market(s)

mexican manufacturers in the automobile/aerospace industry

Industry/Entity Type

Industrial

Colors
ffffff
0555a3

```html
<!DOCTYPE html>
<html lang="en">
<head>
<meta charset="utf-8">
<title>Korvel Business Card</title>
<link rel="stylesheet" href="https://fonts.googleapis.com/css2?family=Archivo:wght@400;500;700;800;900&display=swap">
<style>
  :root {
    --stage: #e9e9ec;
    --card-white: #ffffff;
    --card-grey: #ececec;
    --brand-blue: #2b3fbf;
    --brand-blue-deep: #1c2c9c;
    --brand-blue-light: #3a55d0;
    --text-grey: #6b6b6b;
    --rule-grey: #cfcfcf;
    --white: #ffffff;
  }
  * { margin: 0; padding: 0; box-sizing: border-box; }
  html, body { width: 1200px; height: 780px; overflow: hidden; }
  body {
    background: var(--stage);
    font-family: "Archivo", Arial, sans-serif;
    position: relative;
  }

  /* Front card (portrait) */
  .card-front {
    position: absolute;
    left: 110px; top: 95px;
    width: 340px; height: 590px;
    border-radius: 22px;
    overflow: hidden;
    background: linear-gradient(160deg, var(--card-white) 0%, var(--card-grey) 100%);
    box-shadow: 0 6px 18px rgba(0,0,0,.18);
  }
  .brand {
    position: absolute; top: 78px; left: 0; right: 0;
    text-align: center;
  }
  .brand-name {
    font-size: 60px; font-weight: 900; color: var(--brand-blue);
    letter-spacing: -1px; line-height: 1;
  }
  .person {
    position: absolute; top: 205px; left: 0; right: 0; text-align: center;
  }
  .person-name {
    font-size: 23px; font-weight: 800; color: var(--brand-blue);
    letter-spacing: 1px; text-transform: uppercase;
  }
  .person-title { font-size: 17px; color: var(--text-grey); margin-top: 2px; }
  .contact {
    position: absolute; top: 280px; left: 34px; right: 34px;
    text-align: center;
  }
  .contact-item {
    padding: 10px 0 9px;
    border-top: 1px solid var(--rule-grey);
  }
  .contact-item:last-child { border-bottom: 1px solid var(--rule-grey); }
  .contact-label {
    font-size: 15px; font-weight: 800; color: var(--brand-blue);
  }
  .contact-value {
    font-size: 19px; color: var(--text-grey); margin-top: 2px;
  }
  .contact-value.email { font-size: 16px; }
  .web-band {
    position: absolute; left: 0; right: 0; bottom: 0; height: 92px;
    background: linear-gradient(180deg, var(--brand-blue-light), var(--brand-blue-deep));
    display: flex; align-items: center; justify-content: center;
    color: var(--white); font-size: 19px; font-weight: 500; letter-spacing: .5px;
  }

  /* Back card (landscape) */
  .card-back {
    position: absolute;
    left: 520px; top: 215px;
    width: 590px; height: 340px;
    border-radius: 22px;
    overflow: hidden;
    background: radial-gradient(circle at 70% 25%, var(--brand-blue-light) 0%, var(--brand-blue) 45%, var(--brand-blue-deep) 100%);
    box-shadow: 0 6px 18px rgba(0,0,0,.22);
    color: var(--white);
  }
  .sectors {
    position: absolute; top: 48px; left: 52px; right: 40px;
    font-size: 15px; line-height: 1.35; color: var(--white);
  }
  .back-name {
    position: absolute; left: 48px; top: 115px;
    font-size: 150px; font-weight: 900; letter-spacing: -4px;
    line-height: 1; color: var(--white);
  }
</style>
</head>
<body>
  <section class="card-front" aria-label="Business card front">
    <div class="brand">
      <span class="brand-name">Korvel</span>
    </div>
    <div class="person">
      <div class="person-name">Daniel Reyes</div>
      <div class="person-title">Manager</div>
    </div>
    <div class="contact">
      <div class="contact-item">
        <div class="contact-label">Phone</div>
        <div class="contact-value">(555) 210 - 4830</div>
      </div>
      <div class="contact-item">
        <div class="contact-label">Fax</div>
        <div class="contact-value">(555) 210 - 4831</div>
      </div>
      <div class="contact-item">
        <div class="contact-label">Email</div>
        <div class="contact-value email">sales@korvelpartsco.com</div>
      </div>
    </div>
    <div class="web-band">www.korvelpartsco.com</div>
  </section>

  <section class="card-back" aria-label="Business card back">
    <div class="sectors">
      Steel Mills | Petrochemical | Wood and Paper | Oil Gas Chemical<br>
      Plastic and Rubber | Food and Beverages | Automotive | Utility
    </div>
    <div class="back-name">Korvel</div>
  </section>
</body>
</html>
```